Business card design for Brivo Engineering Tandem

We need a new business card design along with all the necessary to place an order. The company is Brivo Engineering Tandem and we recently updated our logo.

```html
<!DOCTYPE html>
<html lang="en">
<head>
<meta charset="utf-8">
<title>Brivo Engineering Tandem – Business Card</title>
<link href="https://fonts.googleapis.com/css2?family=Poppins:wght@400;500;700&display=swap" rel="stylesheet">
<style>
  :root {
    --backdrop: #1d1d1e;
    --card: #2f2f30;
    --brand-grey: #9a9a9a;
    --band-grey: #a2a2a2;
    --accent: #e8c21c;
    --text-light: #e6e6e6;
  }
  * { box-sizing: border-box; margin: 0; padding: 0; }
  html, body { width: 1200px; height: 689px; overflow: hidden; }
  body {
    background: var(--backdrop);
    font-family: "Poppins", sans-serif;
    position: relative;
  }
  .card {
    position: absolute;
    top: 195px;
    width: 520px;
    height: 300px;
    background: var(--card);
    border-radius: 18px;
    overflow: hidden;
    box-shadow: 0 18px 40px rgba(0,0,0,.45);
  }
  .card--front { left: 50px; }
  .card--back { left: 630px; }

  .wordmark {
    display: flex;
    align-items: center;
    gap: 12px;
    color: var(--brand-grey);
    font-weight: 700;
    text-transform: uppercase;
    letter-spacing: 2px;
    line-height: 1.05;
  }
  .wordmark__square {
    width: 16px; height: 16px;
    background: var(--accent);
    flex: none;
  }
  .card--front .wordmark {
    position: absolute;
    left: 50%; top: 50%;
    transform: translate(-50%, -50%);
    font-size: 30px;
    white-space: nowrap;
  }
  .card--back .wordmark {
    position: absolute;
    left: 44px; top: 42px;
    font-size: 22px;
    white-space: nowrap;
  }
  .card--back .wordmark__square { width: 13px; height: 13px; }

  .holder {
    position: absolute;
    left: 44px; top: 150px;
    padding-left: 26px;
  }
  .holder__bar {
    position: absolute;
    left: 0; top: 4px;
    width: 13px; height: 46px;
    background: var(--accent);
  }
  .holder__name {
    color: var(--accent);
    font-weight: 700;
    font-size: 22px;
    letter-spacing: .5px;
    text-transform: uppercase;
    line-height: 1.15;
  }
  .holder__title {
    color: var(--text-light);
    font-size: 13px;
    letter-spacing: 1px;
    text-transform: uppercase;
  }

  .contacts {
    position: absolute;
    left: 70px; top: 218px;
    list-style: none;
  }
  .contacts li {
    display: flex; align-items: center; gap: 8px;
    color: var(--text-light);
    font-size: 12.5px;
    line-height: 19px;
  }
  .contacts svg { width: 12px; height: 12px; flex: none; }

  .address {
    position: absolute;
    right: 30px; bottom: 62px;
    text-align: right;
    color: var(--text-light);
    font-size: 13px;
    line-height: 1.45;
  }

  .accent-line {
    position: absolute;
    left: 0; bottom: 0;
    width: 330px; height: 7px;
    background: var(--accent);
  }
  .grey-band {
    position: absolute;
    right: 0; bottom: 0;
    width: 190px; height: 42px;
    background: var(--band-grey);
    border-top-left-radius: 28px;
  }
</style>
</head>
<body>

  <section class="card card--front">
    <div class="wordmark">
      <span class="wordmark__square"></span>
      <span>Brivo Engineering Tandem</span>
    </div>
  </section>

  <section class="card card--back">
    <div class="wordmark">
      <span class="wordmark__square"></span>
      <span>Brivo Engineering Tandem</span>
    </div>

    <div class="holder">
      <span class="holder__bar"></span>
      <p class="holder__name">Marcus Hale</p>
      <p class="holder__title">Managing Director</p>
    </div>

    <ul class="contacts">
      <li>
        <svg viewBox="0 0 24 24" fill="var(--accent)"><path d="M6.6 10.8a15.1 15.1 0 0 0 6.6 6.6l2.2-2.2a1 1 0 0 1 1-.25 11.4 11.4 0 0 0 3.6.57 1 1 0 0 1 1 1V20a1 1 0 0 1-1 1A17 17 0 0 1 3 4a1 1 0 0 1 1-1h3.5a1 1 0 0 1 1 1c0 1.25.2 2.45.57 3.57a1 1 0 0 1-.25 1z"/></svg>
        044-555 210 347
      </li>
      <li>
        <svg viewBox="0 0 24 24" fill="var(--accent)"><path d="M2 5h20v14H2z M4 7l8 6 8-6" stroke="var(--card)" stroke-width="1.6"/></svg>
        info@brivotandem.com
      </li>
      <li>
        <svg viewBox="0 0 24 24" fill="none" stroke="var(--accent)" stroke-width="2"><circle cx="12" cy="12" r="10"/><path d="M2 12h20M12 2c3 3 3 17 0 20M12 2c-3 3-3 17 0 20"/></svg>
        www.brivotandem.com
      </li>
    </ul>

    <address class="address" style="font-style:normal">
      48, Harbor Lane<br>
      Eastfield, 204518
    </address>

    <div class="accent-line"></div>
    <div class="grey-band"></div>
  </section>

</body>
</html>
```